RW Holloway LLC Business Card - Civil Engineering & Consulting Firm

We need a Business Card that is elegant, and masculine.  It is our Professional Civil Engineering & Consulting Company located in San Antonio TX (Not s construction or builder firm- no gears & no tool images please). We provide civil engineering services including  commercial site plans, grading and drainage plans, utility plans, hydraulics and hydrology, land planning, utility coordination, and other general civil engineering services related to commercial and residential development.
We have 2 existing Logos. We would like to convey reliability, strength, trustworthiness and attention to detail.  Blues and orange tones as per logo We are OK with the use of a darker blue in the mix.  We have 2 logo versions - Full Company Name Logo to go on the back of card, & Small Icon Logo for the front w/ personal Info.

Target Market(s)
Architects, Real Estate Developers, Other Strctural Engineers, Surveyers, General Contractors
Industry/Entity Type
Professional Civil Engineering
Contact Information for Business Card
Name, Position, Address, Cell & Office #, email, and company website
Font styles to use
Other font styles liked:
- Avian
Requirements
Should not have
- No Tools, No Gears, no Cranes, or Construction Equipment.

```html
<!DOCTYPE html>
<html lang="en">
<head>
<meta charset="utf-8">
<title>RW Holloway LLC Business Card</title>
<link href="https://fonts.googleapis.com/css2?family=Montserrat:wght@400;500;700&family=Josefin+Sans:wght@300;400&display=swap" rel="stylesheet">
<style>
  :root {
    --bg: #8f8f8f;
    --sky: #7aaed6;
    --sky-line: #7fb0db;
    --amber: #ec922f;
    --paper: #f7f7f7;
    --ink: #1c1c1c;
    --white: #ffffff;
  }
  * { margin: 0; padding: 0; box-sizing: border-box; }
  html, body { width: 1200px; height: 900px; overflow: hidden; }
  body {
    background: radial-gradient(circle at 45% 45%, #d6d6d6 0%, var(--bg) 70%, #555 100%);
    position: relative;
    font-family: "Montserrat", sans-serif;
  }
  .card {
    position: absolute;
    left: 250px;
    width: 700px;
    height: 400px;
    border-radius: 28px;
    overflow: hidden;
    box-shadow: 0 10px 24px rgba(0,0,0,.35);
  }
  .card-back {
    top: 35px;
    background: linear-gradient(150deg, var(--sky) 0%, #a9aab0 45%, var(--amber) 85%);
    display: flex;
    flex-direction: column;
    align-items: center;
    justify-content: center;
    color: var(--white);
  }
  .company-block {
    display: flex;
    flex-direction: column;
    align-items: center;
    width: 560px;
  }
  .company-name {
    font-family: "Josefin Sans", sans-serif;
    font-weight: 300;
    font-size: 50px;
    letter-spacing: 5px;
    white-space: nowrap;
    line-height: 1;
  }
  .company-rule {
    width: 100%;
    height: 2px;
    background: var(--white);
    margin: 16px 0 14px;
  }
  .company-tagline {
    font-family: "Josefin Sans", sans-serif;
    font-weight: 300;
    font-size: 20px;
    letter-spacing: 9px;
    white-space: nowrap;
  }
  .card-front {
    top: 465px;
    background: var(--paper);
  }
  .front-bands { position: absolute; inset: 0; }
  .contact {
    position: absolute;
    left: 46px;
    top: 112px;
    color: var(--ink);
  }
  .person-name {
    color: var(--amber);
    font-weight: 700;
    font-size: 26px;
    letter-spacing: 1px;
  }
  .person-role { font-size: 17px; margin-top: 2px; }
  .address { font-size: 15px; line-height: 20px; margin-top: 18px; }
  .contact-list { list-style: none; margin-top: 16px; font-size: 15px; }
  .contact-list li { display: flex; align-items: center; gap: 12px; height: 24px; }
  .contact-list svg { width: 16px; height: 16px; fill: var(--amber); flex: none; }
  .brand-mark {
    position: absolute;
    right: 52px;
    top: 150px;
    display: flex;
    align-items: center;
    gap: 12px;
    color: var(--amber);
    font-weight: 700;
    font-size: 24px;
    white-space: nowrap;
  }
  .brand-square { width: 22px; height: 22px; background: var(--sky); }
</style>
</head>
<body>
  <section class="card card-back">
    <div class="company-block">
      <div class="company-name">RW HOLLOWAY LLC</div>
      <div class="company-rule"></div>
      <div class="company-tagline">CONSULTING ENGINEERS</div>
    </div>
  </section>

  <section class="card card-front">
    <svg class="front-bands" viewBox="0 0 700 400" preserveAspectRatio="none" aria-hidden="true">
      <defs>
        <linearGradient id="band-fade" x1="0" y1="0" x2="1" y2="0">
          <stop offset="0" stop-color="#7aaed6"/>
          <stop offset="0.55" stop-color="#f7f7f7"/>
          <stop offset="1" stop-color="#ec922f"/>
        </linearGradient>
      </defs>
      <polygon points="0,0 700,0 700,18 255,18 230,62 0,62" fill="url(#band-fade)"/>
      <polygon points="262,30 700,30 700,38 258,38" fill="#7fb0db"/>
      <polygon points="0,378 455,378 480,338 700,338 700,400 0,400" fill="url(#band-fade)"/>
      <polygon points="0,362 448,362 444,370 0,370" fill="#7fb0db"/>
    </svg>

    <div class="contact">
      <div class="person-name">DANE WHITLOCK</div>
      <div class="person-role">Co-Founder</div>
      <div class="address">4120 Cedar Bend Drive<br>Suite 210 San Antonio</div>
      <ul class="contact-list">
        <li><svg viewBox="0 0 24 24"><path d="M6.6 10.8a15 15 0 0 0 6.6 6.6l2.2-2.2c.3-.3.7-.4 1-.2 1.1.4 2.3.6 3.6.6.6 0 1 .4 1 1V20c0 .6-.4 1-1 1A17 17 0 0 1 3 4c0-.6.4-1 1-1h3.5c.6 0 1 .4 1 1 0 1.3.2 2.5.6 3.6.1.3 0 .7-.2 1z"/></svg>555-204-0188</li>
        <li><svg viewBox="0 0 24 24"><path d="M3 9c0-3 4-5 9-5s9 2 9 5v2h-5V9H8v2H3zM6 12h12l2 8H4zm6 2a2.5 2.5 0 1 0 0 5 2.5 2.5 0 0 0 0-5z"/></svg>555-204-0190</li>
        <li><svg viewBox="0 0 24 24"><path d="M2 5h20v14H2zm2 2v.4l8 5.2 8-5.2V7zm0 2.8V17h16V9.8l-8 5.2z"/></svg>info@rwhollowayllc</li>
        <li><svg viewBox="0 0 24 24"><path d="M12 2a10 10 0 1 0 0 20 10 10 0 0 0 0-20zm0 2c1 0 2.2 1.9 2.7 5H9.3C9.8 5.9 11 4 12 4zM4.3 11h3a17 17 0 0 0 0 2h-3a8 8 0 0 1 0-2zm5 0h5.4a15 15 0 0 1 0 2H9.3a15 15 0 0 1 0-2zm7.4 0h3a8 8 0 0 1 0 2h-3a17 17 0 0 0 0-2zM9.3 15h5.4c-.5 3.1-1.7 5-2.7 5s-2.2-1.9-2.7-5z"/></svg>www.rwhollowayeng.com</li>
      </ul>
    </div>

    <div class="brand-mark">
      <span class="brand-square"></span>
      <span>RW Holloway LLC</span>
    </div>
  </section>
</body>
</html>
```